Website for a Psychologist in Private Practice

I need a cool web design for my website: www.drkalvoric.com. I would like it to look professional. Keep all the current content and add: Space for video; radio spots (see Silver Cedar Tunes Logo below for those); Quick Inquiry; Friendora link; 5 star rating on Rivo; a map; reviews from former patients. I am open to suggestions.

Target Market(s)

Those seeking individual and marital counseling.

Industry/Entity Type

Mental Health

Number of Pages Required

1 page

Font styles to use
Sans Serif
Other font styles liked:
• I'm open but no hard to read script

Requirements
Must have
• All the content on my home page with link for video and radio spots. List services and degrees and expertices (pics not necessary).
Nice to have
• A video of me and radio conversations (logo of Silver Cedar Tunes radio attached).
Should not have
• Cartoons, comedy, etc.... I don't need pictures of services (marital, depression, etc...) Just list those.

```html
<!DOCTYPE html>
<html lang="en">
<head>
<meta charset="utf-8">
<title>Dr. Dana R. Kalvoric – Psychologist</title>
<link href="https://fonts.googleapis.com/css2?family=Signika:wght@400;600&family=Roboto:ital,wght@0,400;0,500;1,400;1,700&display=swap" rel="stylesheet">
<style>
:root{
  --blue:#2f82c8;
  --blue-dark:#1f6aa8;
  --brand:#2a7fc0;
  --ink:#222;
  --white:#fff;
  --panel:rgba(30,55,70,.55);
  --band:rgba(18,50,52,.78);
  --reviews:rgba(70,64,58,.82);
  --footer:#2b2a29;
  --muted:#c9c9c9;
}
*{box-sizing:border-box;margin:0;padding:0}
html,body{width:743px;height:1200px;overflow:hidden}
body{position:relative;font-family:"Roboto",sans-serif;color:var(--ink);background:#fff}
.abs{position:absolute}
.head-font{font-family:"Signika",sans-serif}

/* header */
.topline{left:0;top:0;width:743px;height:2px;background:var(--blue)}
.logo{left:83px;top:16px;font-family:"Signika",sans-serif;font-size:23px;color:var(--brand)}
.license{left:445px;top:33px;font-size:8.5px;color:#333}
.call{left:552px;top:18px}
.call-label{left:576px;top:18px;font-size:9.5px;color:#222}
.call-number{left:578px;top:30px;font-size:14px;color:var(--brand)}

/* nav */
.nav{left:0;top:58px;width:743px;height:28px;background:var(--blue)}
.nav a{position:absolute;top:0;height:28px;line-height:28px;font-size:10px;color:var(--white);text-decoration:none;font-family:"Signika",sans-serif}
.nav a.active{color:#10263a;text-decoration:underline;text-underline-offset:3px}
.nav .sep{position:absolute;top:0;width:1px;height:28px;background:rgba(255,255,255,.25)}
.follow{position:absolute;left:558px;top:0;line-height:28px;font-size:8px;color:#fff}
.social{position:absolute;top:0;line-height:28px;font-size:8px;color:#fff}

/* hero */
.hero{left:0;top:86px;width:743px;height:272px;background:linear-gradient(100deg,#e2dac8 0%,#efe8d6 40%,#f3ead2 70%,#e6d9b7 100%)}
.hero-art{left:340px;top:86px;width:403px;height:272px;background:radial-gradient(ellipse at 60% 45%,rgba(250,235,190,.7),rgba(230,215,180,0) 70%)}
.hero-kicker{left:82px;top:168px;font-family:"Signika",sans-serif;font-size:14px;color:#2f2f2f}
.hero-copy{left:82px;top:194px;width:200px;font-family:"Signika",sans-serif;font-size:14px;line-height:21.5px;color:#3a3a3a}
.arrow{top:212px;width:22px;height:20px;background:#2e2e2e}

/* main */
.beach{left:0;top:358px;width:743px;height:664px;background:linear-gradient(180deg,#7aa8c8 0%,#5fb0c4 22%,#2f9fb0 40%,#6fc3c2 55%,#cfc9b2 75%,#c9b89a 100%)}
.panel{left:82px;top:358px;width:581px;height:484px;background:var(--panel)}
.col-title{font-family:"Signika",sans-serif;font-size:13.5px;line-height:15px;color:#fff}
.rule{height:2px;background:#5aa3d9}
.rule::before{content:"";position:absolute;left:0;top:0;width:60px;height:2px;background:#1d2b35}
.about-text{left:88px;top:428px;width:172px;font-size:8.4px;line-height:13px;color:#fff}
.about-text a{color:#fff}
.avatar{border-radius:50%;border:2px solid #fff;background:linear-gradient(160deg,#d8c49a,#8e7b5e)}
.expert-name{left:357px;top:440px;font-family:"Signika",sans-serif;font-size:14px;line-height:18px;color:#fff}
.checks{left:291px;top:488px;list-style:none;font-size:8.4px;line-height:13px;color:#fff}
.checks li{position:relative;padding-left:11px}
.checks svg{position:absolute;left:0;top:3px}
.quote-box{left:481px;top:429px;width:176px;height:104px;background:rgba(210,215,215,.85);border:1px solid rgba(255,255,255,.6);padding:4px 7px 0 9px;font-size:8.4px;line-height:13px;color:#444}
.quote-mark{font-family:Georgia,serif;font-size:16px;color:#8a8a8a;line-height:8px;vertical-align:-4px}
.quote-by{position:absolute;right:8px;bottom:6px;font-family:Georgia,serif;font-size:7.5px;color:#444}
.link{font-size:9px;color:#fff;text-decoration:underline}

.degrees{left:82px;top:580px;width:581px;height:48px;background:var(--band)}
.degrees-title{left:147px;top:595px;font-family:"Signika",sans-serif;font-size:14px;color:#fff}
.degrees-item{font-size:8.4px;color:#fff}

.video{left:88px;top:678px;width:181px;height:137px;border:2px solid #3f8fd6;background:linear-gradient(150deg,#3c5a3a,#6b7a5c 45%,#35507a)}
.inq-note{left:293px;top:681px;font-size:7.2px;color:#fff}
.field{left:293px;width:172px;height:19px;background:rgba(60,70,72,.75);font-size:7.5px;color:#d0d0d0;padding:5px 7px}
.submit{left:293px;top:798px;width:68px;height:18px;background:var(--blue);color:#fff;font-family:"Signika",sans-serif;font-size:9.5px;line-height:18px;text-align:center}
.poster{left:486px;top:653px;width:162px;height:162px;background:linear-gradient(140deg,#e0306a 0%,#c9475d 30%,#8c6f60 60%,#c4563f 100%)}

.reviews{left:82px;top:842px;width:581px;height:180px;background:var(--reviews)}
.reviews-title{left:82px;top:860px;width:581px;text-align:center;font-family:"Signika",sans-serif;font-size:14px;color:#fff}
.review-text{left:174px;top:902px;width:472px;font-style:italic;font-size:8.2px;line-height:14.5px;color:#fff}
.review-by{left:174px;top:970px;font-style:italic;font-weight:700;font-size:8px;color:#fff}
.more{left:562px;top:982px;font-size:8px;color:#fff}

/* footer */
.footer{left:0;top:1022px;width:743px;height:152px;background:var(--footer)}
.foot-title{font-family:"Signika",sans-serif;font-size:9.5px;color:#fff}
.dash{border-top:1px dashed #6a6a6a}
.foot-links{left:88px;top:1063px;list-style:none;font-size:8px;line-height:13.7px;color:#fff}
.foot-links li:first-child{color:#e88b3a}
.badge{left:212px;width:127px;border:1px solid #8fb6d8}
.contact-row{left:423px;font-size:8px;line-height:11.5px;color:#fff}
.contact-row b{display:inline-block;width:18px;font-weight:400}
.rivo{left:594px;top:1058px;width:51px;height:50px;border-radius:7px;background:#c9302b;border:2px solid #e9e2dc}
.share{left:591px;top:1120px;width:57px;height:19px;background:#3b5e9c;border-radius:2px;color:#fff;font-size:8px;line-height:19px;text-align:center}
.copyright{left:0;top:1174px;width:743px;height:26px;background:var(--blue);color:#fff;font-size:8px;line-height:26px;text-align:center}
</style>
</head>
<body>

<!-- header -->
<div class="abs topline"></div>
<div class="abs logo">Dr. Dana R. Kalvoric</div>
<div class="abs license">California # PSY20581</div>
<svg class="abs call" width="20" height="20" viewBox="0 0 20 20" aria-hidden="true">
  <circle cx="10" cy="10" r="9" fill="none" stroke="#2a7fc0" stroke-width="1.2"/>
  <path d="M7 5.5c-1 .6-1.4 1.8-.8 3.3.9 2.3 2.6 4.1 4.6 5 1.3.6 2.4.2 3-.7l-1.6-1.6-1.2.7c-1.1-.5-2.2-1.6-2.8-2.8l.7-1.2z" fill="#2a7fc0"/>
</svg>
<div class="abs call-label">Call Us Today</div>
<div class="abs call-number">555-014-2290</div>

<!-- navigation -->
<nav class="abs nav">
  <a class="active" style="left:88px">Home</a>
  <span class="sep" style="left:122px"></span>
  <a style="left:135px">About Me</a>
  <span class="sep" style="left:187px"></span>
  <a style="left:198px">Sessions</a>
  <span class="sep" style="left:248px"></span>
  <a style="left:259px">Resources</a>
  <span class="sep" style="left:317px"></span>
  <a style="left:328px">BIO</a>
  <span class="sep" style="left:354px"></span>
  <a style="left:365px">Customer Reviews</a>
  <span class="sep" style="left:458px"></span>
  <a style="left:471px">Contact Us</a>
  <span class="follow">Follow Us On</span>
  <span class="social" style="left:614px">Friendora</span>
  <span class="social" style="left:657px">Chirply</span>
</nav>

<!-- hero -->
<div class="abs hero"></div>
<div class="abs hero-art" role="img" aria-label="Photo of a highlighter marking the words mediation and dispute resolution process"></div>
<div class="abs hero-kicker">DO NOT COMPROMISE</div>
<div class="abs hero-copy">Experience separates good psychologists from others with fewer and more proficient sessions</div>
<svg class="abs arrow" style="left:4px" viewBox="0 0 22 20" aria-hidden="true"><rect width="22" height="20" fill="#2e2e2e"/><path d="M13 5l-5 5 5 5" stroke="#fff" stroke-width="2" fill="none"/></svg>
<svg class="abs arrow" style="left:714px" viewBox="0 0 22 20" aria-hidden="true"><rect width="22" height="20" fill="#2e2e2e"/><path d="M9 5l5 5-5 5" stroke="#fff" stroke-width="2" fill="none"/></svg>

<!-- main content -->
<div class="abs beach" role="img" aria-label="Background photo of a tropical beach with sea and sky"></div>
<div class="abs panel"></div>

<div class="abs col-title" style="left:90px;top:382px">About<br>Dr. Dana R. Kalvoric</div>
<div class="abs rule" style="left:88px;top:415px;width:173px"></div>
<div class="abs about-text">While I acknowledge the importance of my education, I also appreciate the role my experiences have played in allowing me to relate so well to others. Allow me to share those I feel are most relevant with you.<br>I survived an abusive childhood that my mother &amp; sister unfortunately did not. &amp; it was my grief &amp; desire to become stronger than my past that led me to counseling.....<br><a>Read More</a></div>

<div class="abs col-title" style="left:288px;top:382px">My<br>Expertise</div>
<div class="abs rule" style="left:288px;top:415px;width:173px"></div>
<div class="abs avatar" role="img" aria-label="Portrait photo of the psychologist" style="left:285px;top:422px;width:64px;height:64px"></div>
<div class="abs expert-name">Dr. Dana R.<br>Kalvoric</div>
<ul class="abs checks">
  <li><svg width="8" height="7" viewBox="0 0 8 7"><path d="M.5 3.5l2.3 2.3L7.5.8" stroke="#fff" stroke-width="1.4" fill="none"/></svg>Dating, Marriage,</li>
  <li><svg width="8" height="7" viewBox="0 0 8 7"><path d="M.5 3.5l2.3 2.3L7.5.8" stroke="#fff" stroke-width="1.4" fill="none"/></svg>Parenting &amp; Professional Relationships</li>
  <li><svg width="8" height="7" viewBox="0 0 8 7"><path d="M.5 3.5l2.3 2.3L7.5.8" stroke="#fff" stroke-width="1.4" fill="none"/></svg>Depression &amp; Anxiety Issues</li>
  <li><svg width="8" height="7" viewBox="0 0 8 7"><path d="M.5 3.5l2.3 2.3L7.5.8" stroke="#fff" stroke-width="1.4" fill="none"/></svg>Personality Disorders</li>
  <li><svg width="8" height="7" viewBox="0 0 8 7"><path d="M.5 3.5l2.3 2.3L7.5.8" stroke="#fff" stroke-width="1.4" fill="none"/></svg>Life Management</li>
</ul>

<div class="abs col-title" style="left:481px;top:382px">Radio<br>Conversations</div>
<div class="abs rule" style="left:481px;top:415px;width:174px"></div>
<div class="abs quote-box"><span class="quote-mark">&ldquo;</span> Lorem ipsum dolor sit ae onsectetuer adipiscing elit, sed diam nonummy nibh euis tincidunt ut laoreetlore gna aliquam erat olutpat. Ut wisi enim adinim veniam, quis strud xerci tation ullamrper suscipit lobortis sl ut al lorem.<span class="quote-by">Mara Quinn</span></div>
<div class="abs link" style="left:481px;top:541px">View All</div>

<div class="abs degrees"></div>
<div class="abs degrees-title">My Degrees</div>
<svg class="abs" style="left:228px;top:586px" width="10" height="36" viewBox="0 0 10 36" aria-hidden="true"><path d="M1 1c4 0 4 3 4 8s0 8 4 9c-4 1-4 4-4 9s0 8-4 8" stroke="#aab" stroke-width="1.2" fill="none"/></svg>
<div class="abs degrees-item" style="left:252px;top:591px">Doctoral Degree in Clinical Psychology</div>
<div class="abs degrees-item" style="left:252px;top:608px">Masters Degree in Counseling Psychology</div>
<div class="abs degrees-item" style="left:442px;top:591px">Doctoral Internship, Westbay Medical Center</div>
<div class="abs degrees-item" style="left:442px;top:608px">Masters Internship, Lindell Clinic</div>

<div class="abs col-title" style="left:88px;top:650px">View Video</div>
<div class="abs rule" style="left:88px;top:668px;width:181px"></div>
<div class="abs video" role="img" aria-label="Video still of the psychologist"></div>
<svg class="abs" style="left:160px;top:738px" width="18" height="18" viewBox="0 0 18 18" aria-hidden="true"><circle cx="9" cy="9" r="8" fill="none" stroke="#fff" stroke-width="1.4"/><path d="M7 5.5v7l5.5-3.5z" fill="#fff"/></svg>

<div class="abs col-title" style="left:293px;top:650px">Quick Inquiry</div>
<div class="abs rule" style="left:293px;top:668px;width:172px"></div>
<div class="abs inq-note">Lorem ipsum dolor sit amet, consectetuer</div>
<div class="abs field" style="top:696px">Name</div>
<div class="abs field" style="top:718px">Email</div>
<div class="abs field" style="top:740px">Phone</div>
<div class="abs field" style="top:761px;height:32px">Message</div>
<div class="abs submit">SUBMIT</div>

<div class="abs poster" role="img" aria-label="Silver Cedar Tunes radio show poster, Sundays 4PM PST / 7PM EST"></div>

<div class="abs reviews"></div>
<div class="abs reviews-title">Reviews From Former Patients</div>
<div class="abs" style="left:277px;top:881px;width:188px;height:1px;background:#ddd"></div>
<div class="abs" style="left:349px;top:880px;width:46px;height:2px;background:#3f8fd6"></div>
<div class="abs avatar" role="img" aria-label="Portrait photo of a former patient" style="left:88px;top:896px;width:72px;height:72px;background:linear-gradient(160deg,#c9ced2,#2a3440)"></div>
<div class="abs" style="left:170px;top:894px;font-family:Georgia,serif;font-size:22px;color:#8a8580">&ldquo;</div>
<div class="abs review-text">&nbsp;&nbsp;&nbsp;&nbsp;&nbsp;&nbsp;&nbsp;Lorem ipsum dolor sit amet, consectetuer adipiscing elit, sed diam nonummy nibh euismod tincidunt ut laoreet dolore magna aliquam erat volutpat. Ut wisi enim ad minim veniam, quis nostrud exerci tation ullamcorper suscipit lobortis nisl ut aliquip commodo consequat. Duis autem vel eum iriure dolor in hendrerit in vulputate velit esse molestie consequat, vel illum dolore eu feugiat nulla facilisis at vero eros et accumsan et iusto odio dignissimaugue duis dolore te feugait nulla facilisi.</div>
<div class="abs review-by">.... Lorem Ispum, Manger</div>
<div class="abs more"><u>Read more testimonials</u> &raquo;</div>

<!-- footer -->
<footer class="abs footer"></footer>
<div class="abs foot-title" style="left:88px;top:1039px">Quick Links</div>
<div class="abs dash" style="left:88px;top:1054px;width:72px"></div>
<ul class="abs foot-links">
  <li>Home</li><li>About Me</li><li>Sessions</li><li>Resources</li><li>BIO</li><li>Customer Reviews</li><li>Contact Me</li>
</ul>

<div class="abs foot-title" style="left:212px;top:1039px">A Portion of All Revenue Is Donated To</div>
<div class="abs dash" style="left:212px;top:1054px;width:156px"></div>
<div class="abs badge" style="top:1061px;height:49px;background:#fff" role="img" aria-label="Hearthlight Kids partner badge"></div>
<div class="abs badge" style="top:1115px;height:47px;background:#8fa63c" role="img" aria-label="Maple Haven partner badge"></div>

<div class="abs foot-title" style="left:423px;top:1039px">Contact Details</div>
<div class="abs dash" style="left:423px;top:1054px;width:118px"></div>
<div class="abs contact-row" style="top:1064px"><b>A:</b>418 Larkspur Lane, Suite 210<br><b></b>Harbor Point, CA 92711</div>
<div class="abs contact-row" style="top:1099px"><b>P:</b>555-014-2290</div>
<div class="abs contact-row" style="top:1120px"><b>TF:</b>555-014-2290</div>
<div class="abs contact-row" style="top:1141px"><b>E:</b>dk@drkalvoric.com</div>

<div class="abs rivo" role="img" aria-label="Rivo five star rating badge"></div>
<div class="abs share">Friendora</div>

<div class="abs copyright">Copyright © 2016 Dr. Dana R. Kalvoric &nbsp;All rights reserved</div>

</body>
</html>
```